New Business Card Design Project

Use the flyer uploaded and website www.brightoakbuilders.com for inspiration.
List Our Services on Backside of business cards
Marcus Delling
Harborline Builders Inc.
Licensed General Contractors
858-471-6093

Contact Information for Business Card

Use the flyer uploaded and website www.brightoakbuilders.com for inspiration. List Our Services on Backside of business cards Marcus Delling Harborline Builders Inc. Licensed General Contractors 858-471-6093

```html
<!DOCTYPE html>
<html lang="en">
<head>
<meta charset="utf-8">
<title>Harborline Builders – Business Card</title>
<link rel="stylesheet" href="https://fonts.googleapis.com/css2?family=Cinzel:wght@600&family=Montserrat:wght@400;500&display=swap">
<style>
  :root {
    --page: #1c1c1e;
    --card: #141416;
    --ink: #f4f4f4;
    --ink-soft: #d8d8d8;
  }
  * { box-sizing: border-box; margin: 0; padding: 0; }
  html, body { width: 1200px; height: 912px; overflow: hidden; background: var(--page); }
  body {
    display: flex; flex-direction: column; align-items: center; justify-content: center;
    gap: 30px; font-family: "Montserrat", sans-serif; color: var(--ink);
  }
  .card {
    position: relative; width: 720px; height: 411px;
    background: var(--card); border-radius: 14px;
    box-shadow: 0 12px 30px rgba(0,0,0,.55);
  }
  .brand {
    display: flex; align-items: center; gap: 12px;
    font-family: "Montserrat", sans-serif; font-weight: 500;
    font-size: 26px; letter-spacing: .12em; text-transform: uppercase; color: var(--ink);
  }
  .brand-mark { width: 14px; height: 14px; background: var(--ink); }

  /* back side */
  .card-back { display: flex; flex-direction: column; align-items: center; justify-content: center; gap: 64px; }
  .services { text-align: center; font-size: 21px; line-height: 1.55; color: var(--ink); }

  /* front side */
  .card-front .brand { position: absolute; left: 52px; top: 120px; font-size: 22px; }
  .holder { position: absolute; right: 40px; top: 46px; text-align: right; }
  .holder-name { font-family: "Cinzel", serif; font-weight: 600; font-size: 26px; letter-spacing: .04em; }
  .holder-role { font-size: 16px; margin-top: 4px; color: var(--ink-soft); }
  .edge-bar { position: absolute; right: 0; top: 44px; width: 14px; height: 36px; background: var(--ink); }
  .contacts { position: absolute; left: 52px; top: 238px; list-style: none; }
  .contacts li { display: flex; align-items: center; gap: 12px; font-size: 19px; line-height: 1.6; }
  .contacts svg { width: 16px; height: 16px; flex: none; }
  .company { position: absolute; left: 52px; bottom: 40px; font-size: 20px; }
</style>
</head>
<body>
  <section class="card card-back">
    <div class="brand"><span class="brand-mark"></span>Harborline Builders</div>
    <p class="services">
      Painting • Flooring • Kitchens • Custom Renovations<br>
      Bathrooms • Energy Efficienct Upgrades
    </p>
  </section>

  <section class="card card-front">
    <span class="edge-bar"></span>
    <div class="holder">
      <p class="holder-name">MARCUS DELLING</p>
      <p class="holder-role">Licensed General Contractors</p>
    </div>
    <div class="brand"><span class="brand-mark"></span>Harborline Builders</div>
    <ul class="contacts">
      <li>
        <svg viewBox="0 0 16 16" aria-hidden="true"><circle cx="8" cy="8" r="8" fill="#f4f4f4"/><path d="M5 4.5l1.6-.3.8 2-1 .7a5 5 0 0 0 2.7 2.7l.7-1 2 .8-.3 1.6c-3.6.3-6.8-2.9-6.5-6.5z" fill="#141416"/></svg>
        858-471-6093
      </li>
      <li>
        <svg viewBox="0 0 16 16" aria-hidden="true"><rect x="1" y="3.5" width="14" height="9" rx="1" fill="#f4f4f4"/><path d="M1.5 4l6.5 5 6.5-5" stroke="#141416" stroke-width="1.2" fill="none"/></svg>
        info@brightoakbuilders.com
      </li>
      <li>
        <svg viewBox="0 0 16 16" aria-hidden="true"><circle cx="8" cy="8" r="7.5" fill="#f4f4f4"/><g stroke="#141416" stroke-width="1" fill="none"><ellipse cx="8" cy="8" rx="3" ry="7"/><path d="M1 8h14M2.5 4.5h11M2.5 11.5h11"/></g></svg>
        www.brightoakbuilders.com
      </li>
    </ul>
    <p class="company">Harborline Builders Inc.</p>
  </section>
</body>
</html>
```